Brochure for a paper wholesaler who wants to educate his print industry clients

We will be making a stapled informative brochure, that contains basic information about our paper products - the types of paper there is, their characteristics and other useful information.
As we are part of a paper wholesaler group in Europe - ORVALT, we received a brochure in German that has this kind of information. The text in it is not as important. What is important is the layout of the document and how the text will appear in it (added in the uploaded files - 210915_Wiessenswertes_TBKU_H73.pdf).
We are allowed to tinker with this file and adjust it to our needs. So there are also .idml and .indd files available (also in the uploaded files).
We would like to keep the custom page size of 210 x290mm (8.3x11.4 in), or you can go up to 210x297mm (8.3x11.7 in).
What we want is a modern looking design that contains our companies red bordo and white/ grey colours to replace the existing green colours in this borchure. The pictures and appearance of the file can be changed according to your views and what you think would look good. We don't necessarily want to keep the same design, we just want the layout of the document be the same, as we will be placing our translated text into it. The ORVALT logo should be replaced with our own logo (KENDRO Logo.png).
As for how it could look, it could go together with our paper presentation, for which the design can be seen in the "KENDRO Base - v2.pptx".
Holiday season, so have a lot of tasks to take care of and not as much time to check MakerHive as often.

```html
<!DOCTYPE html>
<html lang="de">
<head>
<meta charset="utf-8">
<title>Broschüre – Inhalt und Fachlatein</title>
<link href="https://fonts.googleapis.com/css2?family=Poppins:wght@400;500;600;700;800&display=swap" rel="stylesheet">
<style>
  :root{
    --bordo:#8b2e33;
    --ink:#1d1d1d;
    --paper:#ffffff;
    --row-light:#efefef;
    --row-dark:#dcdcdc;
    --stage:#101010;
  }
  *{margin:0;padding:0;box-sizing:border-box}
  html,body{width:1200px;height:1200px;overflow:hidden;background:var(--stage)}
  body{position:relative;font-family:'Poppins',sans-serif;color:var(--ink)}
  .page{position:absolute;background:var(--paper);overflow:hidden}
  .page--left{left:39px;top:170px;width:565px;height:780px}
  .page--right{left:612px;top:171px;width:565px;height:780px}

  .hero{position:absolute;left:0;top:0;width:402px;height:235px;
    clip-path:polygon(0 0,100% 0,100% 100%,163px 100%,0 28px);
    background:linear-gradient(135deg,#0d4f9a 0%,#0a7fb8 35%,#3fc4cc 55%,#8fdde0 70%,#1a8fc4 100%)}
  .rule-v{position:absolute;left:48px;width:2px;background:var(--bordo)}
  .rule-v--top{top:88px;height:158px}
  .rule-v--bottom{top:506px;height:274px}
  .toc-title{position:absolute;left:48px;top:265px;font-size:31px;font-weight:800;color:var(--bordo);letter-spacing:-0.3px}
  .toc{position:absolute;left:50px;top:312px;width:480px;list-style:none}
  .toc li{display:flex;align-items:baseline;height:19px;font-size:12.6px;font-weight:400}
  .toc .dots{flex:1;margin:0 6px;height:3px;transform:translateY(-1px);
    background-image:radial-gradient(circle,#333 0.9px,transparent 1.1px);
    background-size:4.6px 3px;background-repeat:repeat-x}
  .toc .num{width:14px;text-align:right}
  .folio{position:absolute;font-size:7px;font-weight:700;color:var(--bordo)}
  .page--left .folio{left:27px;top:746px}

  .rule-h{position:absolute;left:40px;right:0;top:48px;height:2px;background:var(--bordo)}
  .section-title{position:absolute;left:40px;top:58px;font-size:18.5px;font-weight:700;color:var(--bordo);letter-spacing:0.1px}
  .bar{position:absolute;left:40px;width:466px;height:19px;background:var(--bordo);color:#fff;
    font-size:12.4px;font-weight:500;padding-left:6px;line-height:19px}
  .bar--terms{top:89px}
  .bar--abbr{top:367px}
  .bar .toggle{position:absolute;right:-8px;top:1px;width:17px;height:17px;border-radius:50%;background:#fff;border:1.5px solid var(--bordo)}
  .bar .toggle svg{position:absolute;left:3px;top:4px}

  .table{position:absolute;left:40px;width:478px;font-size:9.6px;line-height:12.4px}
  .table .row{display:flex;align-items:center}
  .table .row:nth-child(odd){background:var(--row-light)}
  .table .row:nth-child(even){background:var(--row-dark)}
  .terms{top:110px}
  .terms .row{height:33px}
  .terms dt{width:160px;padding-left:6px;font-weight:700;font-size:9.8px}
  .terms dd{width:312px;font-size:9.3px;letter-spacing:-0.15px;word-spacing:-0.5px;text-align:justify;text-align-last:left}
  .abbr{top:387px}
  .abbr .row{height:25px;align-items:flex-start;padding-top:6px}
  .abbr .row.tall{height:33px}
  .abbr .code{width:72px;padding-left:6px;font-weight:700;font-size:9.6px}
  .abbr .en{width:159px}
  .abbr .de{width:236px}

  .brand{position:absolute;left:40px;top:741px;display:flex;align-items:center;gap:14px}
  .brand .mark{width:24px;height:24px;border:1.5px solid var(--bordo)}
  .brand .name{font-size:12px;font-weight:500;letter-spacing:12px;color:var(--bordo)}
  .tagline{position:absolute;right:55px;top:746px;font-size:7px;font-weight:700;letter-spacing:1.2px}
  .page--right .folio{left:536px;top:746px}
</style>
</head>
<body>
  <section class="page page--left">
    <div class="hero" role="img" aria-label="Foto: gerollte Papierbögen in Blau- und Türkistönen"></div>
    <div class="rule-v rule-v--top"></div>
    <h1 class="toc-title">Inhalt</h1>
    <ol class="toc">
      <li>Fachlatein für Fortgeschrittene<span class="dots"></span><span class="num">03</span></li>
      <li>Karton im Überblick<span class="dots"></span><span class="num">04</span></li>
      <li>Das kleine 1x1 der Formatschule<span class="dots"></span><span class="num">04</span></li>
      <li>Umfangreiche Sache<span class="dots"></span><span class="num">05</span></li>
      <li>Hilfe bei Gewichtsproblemen<span class="dots"></span><span class="num">06</span></li>
      <li>Die feine Art zu drucken<span class="dots"></span><span class="num">07</span></li>
      <li>Wegweiser für die Laufrichtung<span class="dots"></span><span class="num">08</span></li>
      <li>Garantierte Farben<span class="dots"></span><span class="num">10</span></li>
      <li>Natürlich der Umwelt zuliebe<span class="dots"></span><span class="num">10</span></li>
    </ol>
    <div class="rule-v rule-v--bottom"></div>
    <span class="folio">2</span>
  </section>

  <section class="page page--right">
    <div class="rule-h"></div>
    <h2 class="section-title">FACHLATEIN FÜR FORTGESCHRITTENE</h2>

    <div class="bar bar--terms">Die gebräuchlichsten Fachbegriffe und Abkürzungen
      <span class="toggle"><svg width="9" height="6" viewBox="0 0 9 6"><path d="M1 1l3.5 3.5L8 1" fill="none" stroke="#8b2e33" stroke-width="1.6"/></svg></span>
    </div>
    <dl class="table terms">
      <div class="row"><dt>ungestrichen</dt><dd>Unveredelte, maschinenglatte oder satinierte Papiere, die aus verschiedenen Faserstoffen hergestellt werden können.</dd></div>
      <div class="row"><dt>satiniert/ scharf satiniert</dt><dd>In einem Kalander nachträglich und unterschiedlich stark geglättete Papiere.</dd></div>
      <div class="row" style="height:45px"><dt>gestrichen</dt><dd>Die Oberfläche des Papiers wird bereits in der Papiermaschine oder nachträglich in einer Streichmaschine durch einen Strichauftrag veredelt. Daraus ergibt sich eine bessere Druckwiedergabe.</dd></div>
      <div class="row"><dt>matt gestrichen</dt><dd>Die Oberfläche des Papiers wird in einem zusätzlichen Arbeitsgang mit matten Pigmenten gestrichen.</dd></div>
      <div class="row"><dt>halbmatt gestrichen/<br>gestrichen (silk/satin)</dt><dd>Ein besonderer Strichauftrag und/oder spezielles Kalandrieren erzeugen eine halbmatte Oberfläche.</dd></div>
      <div class="row"><dt>glänzend gestrichen</dt><dd>Durch nachträgliches Satinieren und einen speziellen Strichauftrag entsteht eine glänzende Oberfläche.</dd></div>
      <div class="row"><dt>FCO</dt><dd>In der Papiermaschine (inline) gestrichenes Papier mit matter oder glänzender Oberfläche.</dd></div>
    </dl>

    <div class="bar bar--abbr">Abkürzungen und ihre Übersetzung
      <span class="toggle"><svg width="9" height="6" viewBox="0 0 9 6"><path d="M1 1l3.5 3.5L8 1" fill="none" stroke="#8b2e33" stroke-width="1.6"/></svg></span>
    </div>
    <div class="table abbr">
      <div class="row"><span class="code">WFU</span><span class="en">woodfree, uncoated</span><span class="de">holzfrei ungestrichen</span></div>
      <div class="row"><span class="code">MFS</span><span class="en">machine-finished special</span><span class="de">holzhaltig, maschinenglatt, ungestrichen</span></div>
      <div class="row"><span class="code">WFC</span><span class="en">woodfree, coated</span><span class="de">holzfrei gestrichen</span></div>
      <div class="row tall"><span class="code">MWC</span><span class="en">middleweight, coated</span><span class="de">doppelt gestrichen, holzhaltig, hoher Weißegrad, mittleres Gewicht</span></div>
      <div class="row"><span class="code">LWC</span><span class="en">ightweight, coated</span><span class="de">einfach gestrichen, holzhaltig</span></div>
      <div class="row tall"><span class="code">ULWC</span><span class="en">ultralightweight, coated</span><span class="de">einfach gestrichen, holzhaltig, ultraleichtgewich-tig</span></div>
      <div class="row"><span class="code">MFC</span><span class="en">machine-finished, coated</span><span class="de">maschinenglatt gestrichen, holzhaltig</span></div>
      <div class="row"><span class="code">SC-A PLUS</span><span class="en">supercalendered, bright/white</span><span class="de">superkalandriert, holzhaltig, hoher Weißegrad</span></div>
      <div class="row"><span class="code">SC-A</span><span class="en">supercalendered</span><span class="de">superkalandriert, holzhaltig, Standard</span></div>
      <div class="row"><span class="code">SC-B</span><span class="en">softcalendered</span><span class="de">softkalandriert, holzhalti</span></div>
      <div class="row tall"><span class="code">FCO</span><span class="en">film coated offset</span><span class="de">in der Papiermaschine (inline) gestrichenes Pa-pier</span></div>
      <div class="row"><span class="code">HSWO</span><span class="en">heatset web offset</span><span class="de">Rollenoffset mit Heißlufttrocknung</span></div>
    </div>

    <div class="brand"><span class="mark"></span><span class="name">KENDRO</span></div>
    <span class="tagline">PAPER THAT MOVES YOUR PRINT!</span>
    <span class="folio">3</span>
  </section>
</body>
</html>
```